Need help in designing new business card utilizing our new logo.

BuildMark Solutions works with Construction Business Owners, Managers & IT Professionals to strengthen software usage and increase user productivity.

Our Construction Accounting and Mobile Field Management Software Clients engage with us in the following areas:

New Software Implementations
Software Re-Implementations
Redesigning Software Usage at the User Level
Project Coordination & Management
Continued Software Support

Old tag line:
Weighing Options - Implementing Solutions

www.buildmark-solutions.example

Ridge 4 is a product, but not needed for a new business card.

```html
<!DOCTYPE html>
<html lang="en">
<head>
<meta charset="utf-8">
<title>BuildMark Solutions – Business Card</title>
<link href="https://fonts.googleapis.com/css2?family=Montserrat:wght@400;500;600&display=swap" rel="stylesheet">
<style>
  :root {
    --brand-blue: #262f9b;
    --brand-blue-back: #2c35a3;
    --text-dark: #3a3a3a;
    --card-white: #ffffff;
    --ground: #2a2a2a;
    --faint: #f1f1f3;
  }
  * { margin: 0; padding: 0; box-sizing: border-box; }
  html, body {
    width: 1200px; height: 897px; overflow: hidden;
    background: var(--ground);
    font-family: "Montserrat", sans-serif;
  }
  .stage { position: relative; width: 1200px; height: 897px; }
  .card {
    position: absolute; left: 303px; width: 595px; height: 338px;
    border-radius: 20px; overflow: hidden;
  }
  .card-front { top: 92px; background: var(--card-white); }
  .card-back { top: 469px; background: var(--brand-blue-back); }

  .abs { position: absolute; white-space: nowrap; }

  .brand-front {
    left: 31px; top: 47px; display: flex; align-items: center; gap: 10px;
    color: var(--brand-blue); font-weight: 500; font-size: 26px; letter-spacing: -0.3px;
  }
  .brand-mark { width: 16px; height: 16px; background: var(--brand-blue); }

  .faint-area {
    right: 8px; top: 10px; width: 290px; height: 310px;
    background: radial-gradient(circle at 55% 50%, var(--faint) 0%, rgba(241,241,243,0) 70%);
  }

  .person-name { left: 31px; top: 154px; font-size: 22px; font-weight: 500; color: var(--brand-blue); }
  .person-role { left: 31px; top: 183px; font-size: 15px; color: var(--text-dark); }

  .specialty {
    right: 34px; top: 160px; text-align: right;
    font-size: 15px; line-height: 20px; font-weight: 500; color: var(--brand-blue);
  }
  .rule { left: 31px; top: 214px; width: 530px; height: 1.5px; background: var(--brand-blue); }

  .contacts { left: 31px; top: 222px; list-style: none; }
  .contacts li {
    display: flex; align-items: center; gap: 9px; height: 20px;
    font-size: 14.5px; color: var(--text-dark);
  }
  .contacts svg { width: 11px; height: 11px; flex: none; }

  .address {
    right: 34px; top: 242px; text-align: right;
    font-size: 15px; line-height: 20px; color: var(--text-dark);
  }

  .back-pattern {
    left: 0; top: 0; width: 595px; height: 338px;
    background: linear-gradient(160deg, #3139a8 0%, #2c35a3 55%, #3a43ae 100%);
  }
  .brand-back {
    left: 0; width: 595px; top: 118px; display: flex; justify-content: center; align-items: center; gap: 14px;
    color: var(--card-white); font-weight: 500; font-size: 38px; letter-spacing: -0.5px;
  }
  .brand-back .brand-mark { width: 22px; height: 22px; background: var(--card-white); }
  .services {
    left: 0; width: 595px; top: 227px; text-align: center; list-style: none;
    font-size: 15px; line-height: 20px; color: var(--card-white);
  }
</style>
</head>
<body>
<main class="stage">

  <section class="card card-front" aria-label="Business card front">
    <div class="abs faint-area" role="img" aria-label="Large faint brand decoration"></div>

    <div class="abs brand-front"><span class="brand-mark"></span>BuildMark Solutions</div>

    <h1 class="abs person-name">Dana R. Whitfield</h1>
    <p class="abs person-role">Owner</p>

    <p class="abs specialty">Construction Accounting<br>Software Consultants</p>

    <div class="abs rule"></div>

    <ul class="abs contacts">
      <li>
        <svg viewBox="0 0 12 12" aria-hidden="true"><path d="M2.5 1l2 2.2-1 1.3c.6 1.4 1.6 2.4 3 3l1.3-1 2.2 2-1.3 1.5C5 10 2 7 1 2.3z" fill="var(--brand-blue)"/></svg>
        800-555-0142 ext.100
      </li>
      <li>
        <svg viewBox="0 0 12 12" aria-hidden="true"><rect x="3" y="0.8" width="6" height="10.4" rx="1" fill="none" stroke="var(--brand-blue)" stroke-width="1.4"/><circle cx="6" cy="9.2" r=".7" fill="var(--brand-blue)"/></svg>
        518-555-0193
      </li>
      <li>
        <svg viewBox="0 0 12 12" aria-hidden="true"><rect x="1" y="2.5" width="10" height="7" fill="none" stroke="var(--brand-blue)" stroke-width="1.2"/><path d="M1 2.8l5 3.6 5-3.6" fill="none" stroke="var(--brand-blue)" stroke-width="1.2"/></svg>
        dana.whitfield@buildmark-solutions.example
      </li>
      <li>
        <svg viewBox="0 0 12 12" aria-hidden="true"><g fill="none" stroke="var(--brand-blue)" stroke-width="1"><circle cx="6" cy="6" r="5"/><ellipse cx="6" cy="6" rx="2.2" ry="5"/><path d="M1 6h10M2 3.2h8M2 8.8h8"/></g></svg>
        www.buildmark-solutions.example
      </li>
    </ul>

    <p class="abs address">48B Market Street<br>PMB 117 Lakeview Falls<br>NY 12345</p>
  </section>

  <section class="card card-back" aria-label="Business card back">
    <div class="abs back-pattern" role="img" aria-label="Repeating tonal brand pattern"></div>

    <div class="abs brand-back"><span class="brand-mark"></span>BuildMark Solutions</div>

    <ul class="abs services">
      <li>New Software Implementations | Software Re-Implementations</li>
      <li>Redesigning Software Usage at the User Level</li>
      <li>Project Coordination &amp; Management</li>
      <li>Continued Software Support</li>
    </ul>
  </section>

</main>
</body>
</html>
```